Bookcover: Ways to Turn Into a Bold Pathfinder

I am publishing a super-low-cost innovation book for €4,99 on Quillmere Open Press to help everyone become a great innovator: young ambitious people without college education nor a big budget. Do you want to help me?

Brief:
Design a book cover 1600 x 2560 pixels for QOP.
Main title: Ways to Turn Into a Bold Pathfinder
Sub title: mindset - insights - skills & tools
Author: Joost ter Brakel
Design: captive, and appealing to everyone
Target Group: young ambitious people without college education

For quillmere please format the height/width ratio of 1.6:1

```html
<!DOCTYPE html>
<html lang="en">
<head>
<meta charset="utf-8">
<title>Ways to Turn Into a Bold Pathfinder — Book Cover</title>
<link href="https://fonts.googleapis.com/css2?family=Oswald:wght@500;600&family=Poppins:wght@400;600;800&display=swap" rel="stylesheet">
<style>
  :root {
    --backdrop: #c8c8c8;
    --navy-top: #0c1222;
    --navy-mid: #0f1a33;
    --navy-low: #22253b;
    --cyan: #35e0ff;
    --gold: #e2cf58;
    --white: #ffffff;
    --glow: #2f7fe6;
    --glow-deep: #123a7a;
  }
  * { margin: 0; padding: 0; box-sizing: border-box; }
  html, body {
    width: 1200px; height: 1200px; overflow: hidden;
    background: var(--backdrop);
  }
  .cover {
    position: absolute; left: 262px; top: 57px;
    width: 682px; height: 1092px; overflow: hidden;
    background: linear-gradient(180deg, var(--navy-top) 0%, var(--navy-mid) 55%, #141a32 85%, var(--navy-low) 100%);
    color: var(--white);
    text-align: center;
  }
  .line { position: absolute; left: 0; width: 100%; white-space: nowrap; line-height: 1; }
  .kicker {
    top: 59px; font-family: "Poppins", sans-serif; font-weight: 400;
    font-size: 35px; letter-spacing: 0.01em;
  }
  .title-accent {
    top: 98px; font-family: "Poppins", sans-serif; font-weight: 800;
    font-size: 68px; color: var(--cyan); letter-spacing: -0.01em;
  }
  .title-mid {
    top: 170px; font-family: "Poppins", sans-serif; font-weight: 400;
    font-size: 64px;
  }
  .rule {
    position: absolute; top: 196px; height: 2px; background: var(--white); opacity: .85;
  }
  .rule.left { left: 91px; width: 99px; }
  .rule.right { left: 495px; width: 98px; }
  .title-main {
    top: 228px; font-family: "Oswald", sans-serif; font-weight: 600;
    font-size: 128px; line-height: 1.02; color: var(--gold);
    letter-spacing: -0.01em; text-transform: uppercase;
  }
  .subtitle {
    top: 355px; font-family: "Poppins", sans-serif; font-weight: 600;
    font-size: 32px;
  }
  .artwork {
    position: absolute; left: 60px; top: 405px; width: 562px; height: 570px;
    background: radial-gradient(ellipse 42% 48% at 50% 48%, #6fb6ff 0%, var(--glow) 25%, var(--glow-deep) 60%, rgba(15,26,51,0) 100%);
  }
  .floor {
    position: absolute; left: -60px; top: 922px; width: 802px; height: 260px;
    border-radius: 50% 50% 0 0 / 18% 18% 0 0;
    background: linear-gradient(180deg, #3a4566 0%, #262c45 30%, var(--navy-low) 100%);
  }
  .author {
    top: 1042px; font-family: "Oswald", sans-serif; font-weight: 500;
    font-size: 40px; letter-spacing: 0.22em; text-transform: uppercase;
  }
</style>
</head>
<body>
  <main class="cover">
    <div class="floor"></div>
    <div class="artwork" role="img" aria-label="Glowing blue light bulb with ornate mandala filament radiating rays, standing on a lit surface"></div>

    <h1 class="book-title">
      <span class="line kicker">WAYS TO</span>
      <span class="line title-accent">TURN INTO</span>
      <span class="line title-mid">A BOLD</span>
      <span class="line title-main">Pathfinder</span>
    </h1>
    <span class="rule left"></span>
    <span class="rule right"></span>

    <p class="line subtitle">Mindset - insights - skills &amp; tools</p>
    <p class="line author">Joost ter Brakel</p>
  </main>
</body>
</html>
```